SavannaPlate Web Page Templates

I need two templates designed for a wholesale food/catering business, one template for the home page and the other for detail pages. The overall template should be a simple, clean and clear design. I have provided the existing logo to which the templates should directly relate.
SavannaPlate supplies food based upon traditional Ghanian recipes to a number of stores across Canberra. In addition, SavannaPlate offers catering for public and private functions across the Canberra region.
The colours in the logo represent the national colours of Ghana (yellow, green, red and black) and the website content will also include traditional Ghanian Kente patterns which will add further colour elements to the site. On this basis, the template design needs to be fairly sparse so as not to compete with the colourful content of the website detail pages.
There is no requirement for specific pages to be designed, as these will be handled in the CMS implementation.
The information provided in the Word document is only designed to provide a sense of the intended content of the website, not as a requirement for specific pages to be produced.

Target Market(s)

Retail/Wholesale food

Number of Pages Required

2 page

Font styles to use
Serif

Colors

Designer to choose colors to be used in the design.

Requirements
Must have
• Template must accommodate a responsive design
• The logo provided will form the cornerstone of the design
Nice to have
• There
Should not have
• Please do not solicit for extra work or for alternative logo design.

```html
<!DOCTYPE html>
<html lang="en">
<head>
<meta charset="utf-8">
<title>SavannaPlate – Home</title>
<link href="https://fonts.googleapis.com/css2?family=Titillium+Web:wght@400;600;700&family=Open+Sans:wght@400;600&display=swap" rel="stylesheet">
<style>
:root{
  --red:#9b0d0d;
  --red-bright:#c8281e;
  --ink:#333;
  --grey-text:#555;
  --band:#e4e4e4;
  --panel:#f3f3f3;
  --dark:#1c1c1c;
  --gold:#e0a21a;
}
*{box-sizing:border-box;margin:0;padding:0}
html,body{width:1200px;height:2458px;overflow:hidden;background:#fff}
body{font-family:"Titillium Web",sans-serif;color:var(--ink);position:relative}
.abs{position:absolute}
.center{left:0;width:1200px;text-align:center}

/* header */
.brand{left:145px;top:18px;font-size:38px;font-weight:600;color:var(--red);letter-spacing:1px}
.brand::before{content:"";display:inline-block;width:12px;height:12px;border-radius:50%;background:var(--gold);margin-right:8px;vertical-align:middle}
.nav{right:145px;top:36px;display:flex;gap:32px;font-size:15px}
.nav a{color:#333;text-decoration:none}
.nav a.active{color:var(--red-bright)}

/* hero */
.hero{left:0;top:92px}
.hero-caption{right:145px;top:448px;text-align:right;color:#fff}
.hero-caption .name{font-size:32px;line-height:36px}
.hero-caption .tag{font-size:40px;font-weight:700;line-height:44px}

/* welcome */
.title{font-size:34px;font-weight:600;color:var(--red);letter-spacing:.5px}
.intro{left:144px;width:912px;top:814px;text-align:center;font-size:14px;line-height:24px;color:#444}
.taste{top:888px;font-size:22px}

/* shops */
.shops-head{top:1094px;font-family:"Open Sans",sans-serif;font-size:25px;color:var(--red)}
.shop{height:119px;background:#fff;display:flex;align-items:center;justify-content:center;font-family:"Open Sans",sans-serif;font-size:20px;font-weight:600;color:#333}
.catering{top:1418px;font-family:"Open Sans",sans-serif;font-size:26px;line-height:36px;color:var(--grey-text)}

/* gallery */
.sub{top:1702px;font-size:19px}
.dish{width:218px;height:160px;top:1745px}
.dish-label{top:1897px;width:200px;height:36px;background:var(--red);color:#fff;font-size:15px;line-height:36px;text-align:center}
.offer{left:144px;top:1957px;width:912px;height:79px;background:var(--panel);border:1px solid #ccc;text-align:center;font-size:16px;padding-top:14px;line-height:24px}
.offer .lead{color:var(--red-bright)}

/* contact */
.contact-links{top:2244px;font-size:26px;font-weight:600;color:#222}
.contact-links span{color:var(--red-bright)}
.social{top:2313px;width:44px;height:44px;border-radius:50%;background:var(--red-bright);border:3px solid #fff}
.foot-links{top:2384px;font-size:13px;color:#bbb}
.copy{top:2414px;font-size:12px;color:#bbb}
</style>
</head>
<body>

<header>
  <div class="abs brand">SavannaPlate</div>
  <nav class="abs nav">
    <a class="active" href="#">HOME</a><a href="#">ABOUT US</a><a href="#">SERVICES</a><a href="#">MENU</a><a href="#">LOCATION</a><a href="#">CONTACT US</a>
  </nav>
</header>

<section>
  <svg class="abs hero" width="1200" height="602" viewBox="0 0 1200 602">
    <defs>
      <linearGradient id="heroFill" x1="0" y1="0" x2="1" y2="1">
        <stop offset="0" stop-color="#7a4a2c"/>
        <stop offset=".45" stop-color="#3a2620"/>
        <stop offset=".75" stop-color="#6b2440"/>
        <stop offset="1" stop-color="#8a5a36"/>
      </linearGradient>
    </defs>
    <path role="img" aria-label="Grilled beef skewers on slate with chilli sauce and a fresh salad" d="M0 0H1200V524Q600 690 0 524Z" fill="url(#heroFill)"/>
    <g>
      <circle cx="70" cy="261" r="18" fill="var(--gold)" stroke="#5a3a10" stroke-width="2"/>
      <path d="M75 252L66 261L75 270" fill="none" stroke="#3a2410" stroke-width="3"/>
      <circle cx="1127" cy="261" r="18" fill="var(--gold)" stroke="#5a3a10" stroke-width="2"/>
      <path d="M1122 252L1131 261L1122 270" fill="none" stroke="#3a2410" stroke-width="3"/>
    </g>
  </svg>
  <div class="abs hero-caption"><div class="name">SavannaPlate</div><div class="tag">COMMENCED IN 2004</div></div>
</section>

<section>
  <h1 class="abs center title" style="top:764px">WELCOME TO SAVANNAPLATE</h1>
  <p class="abs intro">Coming from Ghana and with a passion for cooking I realized, through school P&amp;C fundraising, that as well as enjoying my dishes, people wanted to learn more about Ghanaian food. So I started introducing pre-packaged meals at farmers' markets and food festivals to showcase Ghanaian food far and wide. They took off! People relished the exotic flavours. So why don't you give it a go?</p>
  <p class="abs center taste">Have a taste! Enjoy!!</p>
</section>

<svg class="abs" style="left:0;top:940px" width="1200" height="652" viewBox="0 0 1200 652">
  <path role="img" aria-label="Light grey band with subtle woven pattern" d="M0 0Q600 150 1200 0V572Q600 720 0 572Z" fill="var(--band)"/>
</svg>

<section>
  <h2 class="abs center shops-head" style="font-weight:400">Our beautiful freshly made food is available weekly in the following shops :</h2>
  <div class="abs shop" style="left:144px;top:1148px;width:226px">Harvest Lane</div>
  <div class="abs shop" style="left:373px;top:1148px;width:226px">Greenleaf Pantry</div>
  <div class="abs shop" style="left:602px;top:1148px;width:225px">Orchard Market</div>
  <div class="abs shop" style="left:830px;top:1148px;width:226px">Kettle &amp; Crumb</div>
  <div class="abs shop" style="left:259px;top:1270px;width:226px">Northside Grocer</div>
  <div class="abs shop" style="left:488px;top:1270px;width:225px">Hillview Grocer</div>
  <div class="abs shop" style="left:716px;top:1270px;width:226px">Parkway Grocer</div>
  <p class="abs center catering">We also cater for functions, either cocktail or sit-down dining, where we offer<br>special dishes such as jollof rice, garifortor, etc.</p>
</section>

<section>
  <h2 class="abs center title" style="top:1660px">GALLERY</h2>
  <p class="abs center sub">Our casserole dishes include:</p>
  <div class="abs dish" style="left:144px;background:linear-gradient(135deg,#6e4a1e,#d9b84a,#4f6a2a)" role="img" aria-label="Chicken and spinach casserole"></div>
  <div class="abs dish" style="left:375px;background:linear-gradient(135deg,#4a3a30,#7a2a1a,#2a2420)" role="img" aria-label="Spicy beef casserole"></div>
  <div class="abs dish" style="left:606px;background:linear-gradient(135deg,#8aa0b4,#e0b040,#a8bac8)" role="img" aria-label="Black-eyed beans casserole"></div>
  <div class="abs dish" style="left:837px;background:linear-gradient(135deg,#5a4a40,#f2f0ec,#9aa8b8)" role="img" aria-label="Coconut sweets"></div>
  <div class="abs dish-label" style="left:153px">Chicken &amp; Spinach Casserole</div>
  <div class="abs dish-label" style="left:384px">Spicy beef casserole</div>
  <div class="abs dish-label" style="left:615px">Black-eyed beans casserole</div>
  <div class="abs dish-label" style="left:846px">Coconut sweet</div>
  <div class="abs offer"><div class="lead">&#9432; We also offer:</div>Black-eyed beans snacks served with our home made sweet chilli sauce or traditional Ghanaian chilli sauce.</div>
</section>

<svg class="abs" style="left:0;top:2080px" width="1200" height="378" viewBox="0 0 1200 378">
  <path role="img" aria-label="Light grey band with subtle woven pattern" d="M0 0Q600 150 1200 0V378H0Z" fill="var(--band)"/>
  <path d="M0 182Q600 310 1200 182V378H0Z" fill="var(--dark)"/>
</svg>

<footer>
  <h2 class="abs center title" style="top:2198px">CONTACT US</h2>
  <p class="abs center contact-links"><span>www.savannaplate.example</span> or <span>hello@savannaplate.example</span></p>
  <div class="abs social" style="left:550px"></div>
  <div class="abs social" style="left:606px"></div>
  <p class="abs center foot-links">Home &nbsp;|&nbsp; About Us &nbsp;|&nbsp; Services &nbsp;|&nbsp; Menu &nbsp;|&nbsp; Location &nbsp;|&nbsp; Contact Us</p>
  <p class="abs center copy">Copyright © 2019 SavannaPlate. &nbsp; All rights reserved.</p>
</footer>

</body>
</html>
```